brovlanepass.net

Develop a website for brolanepass.net will be a site to sell tickets for concerts, shows, shows, theaters and others. I need a web design easy view, very easy to use and accumulate events by date. The aim is to develop the site was connected to a complex system that is already developed. (Important this page to a robust system was connected via links the idea is to develop only the front view)
Updates

Reason: I need more designs yet we have not made the decision

Target Market(s)

millennials, adults, who want to enjoy concerts and shows

Industry/Entity Type

Event

Number of Pages Required

5+ page

Colors
1b1b1b
aaaaaa
ffffff

Requirements
Must have
• Easy Vista, accumulation of upcoming events, past events. The tabs should have are: 1 Start: In this part of upcoming events occur. You could put a banner on the top and down the events by date. 2. How to order: page with instructions on how to purchase tickets 3. About Us: The company history 4. Contact: Phones and template for contact by mail 5. Our policies: shopping 6. Notice Privacy: Privacy Notice Copoy 7. Centers Sale: physical places where they can purchase tickets Promoters 8. access: Link to a template
Nice to have
• as you can see p www.quimbarostage.net or farunda.net or farunda.org or gallowmerk.net (important this page to a robust system was connected via links the idea is to develop only the front view)
Should not have
• Many things Tangled

```html
<!DOCTYPE html>
<html lang="en">
<head>
<meta charset="utf-8">
<title>Brovlane Pass – Buy and sell tickets</title>
<link href="https://fonts.googleapis.com/css2?family=Montserrat:wght@500;700;800&family=Open+Sans:wght@400;600;700&family=Oswald:wght@500;600&display=swap" rel="stylesheet">
<style>
:root{
  --ink:#1b1b1b;
  --grey:#aaaaaa;
  --white:#ffffff;
  --band:#ebebeb;
  --accent:#e5532a;
  --badge:#9a9a9a;
  --line:#d6d6d6;
  --text:#444444;
}
*{margin:0;padding:0;box-sizing:border-box}
html,body{width:1200px;height:3814px;overflow:hidden}
body{position:relative;background:var(--white);font-family:"Open Sans",Arial,sans-serif;color:var(--ink)}
.abs{position:absolute}

/* header */
.topbar{left:0;top:0;width:1200px;height:56px;background:rgba(20,14,10,.55);z-index:3}
.brand{left:108px;top:0;height:56px;display:flex;align-items:center;gap:8px;color:var(--white);font-family:"Montserrat",sans-serif;font-weight:800;font-size:21px;letter-spacing:.5px}
.brand-dot{width:14px;height:14px;border-radius:50%;background:var(--white)}
.nav{left:313px;top:0;height:56px;display:flex;align-items:center}
.nav a{color:var(--white);text-decoration:none;font-size:12.5px;padding:0 14px;height:56px;line-height:56px}
.nav a.active{background:var(--white);color:var(--ink)}
.social{display:flex;gap:8px;align-items:center}
.social span{width:22px;height:22px;border-radius:50%;background:var(--grey);display:block}
.nav .social{margin-left:10px}

/* hero */
.hero{left:0;top:0;width:1200px;height:660px;background:radial-gradient(ellipse at 55% 25%,#ffd46a 0%,#f08a1c 22%,#a83a0e 48%,#3a1206 75%,#120603 100%)}
.hero-title{left:0;top:398px;width:1200px;text-align:center;color:var(--white);font-size:27px;font-weight:600}
.search{left:325px;top:480px;width:547px;height:52px;background:var(--white);display:flex;align-items:center}
.search svg{margin-left:20px}
.search .field{flex:1;margin-left:14px;font-size:14px;color:#555}
.search .go{width:112px;height:40px;margin-right:6px;background:var(--ink);color:var(--white);font-weight:700;font-size:14px;display:flex;align-items:center;justify-content:center}
.dots{left:0;top:582px;width:1200px;display:flex;justify-content:center;gap:12px}
.dots i{width:9px;height:9px;border-radius:50%;background:var(--white);display:block}
.dots i.on{background:transparent;border:2px solid var(--white);width:13px;height:13px;margin-top:-2px}

/* section heads */
.sec-title{font-family:"Montserrat",sans-serif;font-weight:700;font-size:27px;color:var(--ink);left:132px}
.view-all{right:137px;height:30px;padding:0 16px;background:var(--ink);color:var(--white);font-size:11.5px;font-weight:700;display:flex;align-items:center;letter-spacing:.3px}
.date-pick{left:925px;top:728px;width:138px;height:49px;border:1px solid var(--grey);padding:7px 12px;font-size:9px;color:#777}
.date-pick b{display:block;font-size:12px;font-weight:400;color:var(--ink);margin-top:2px}
.date-pick svg{position:absolute;right:11px;top:16px}

/* cards */
.card{width:291px;height:292px;overflow:hidden}
.card .photo{position:absolute;inset:0}
.card .shade{position:absolute;left:0;right:0;bottom:0;height:130px;background:linear-gradient(to bottom,rgba(0,0,0,0),rgba(0,0,0,.8))}
.card .date{position:absolute;right:0;top:0;width:56px;height:82px;background:var(--badge);color:var(--white);text-align:center;padding-top:5px;line-height:1}
.card .date b{display:block;font-family:"Oswald",sans-serif;font-size:22px;font-weight:600}
.card .date small{display:block;font-size:8px;margin-top:4px;text-transform:uppercase}
.card .date em{display:block;font-style:normal;font-size:11px;margin-top:6px}
.card h3{position:absolute;left:20px;bottom:45px;color:var(--white);font-family:"Oswald",sans-serif;font-weight:600;font-size:19px;letter-spacing:.2px}
.card p{position:absolute;left:20px;bottom:25px;color:var(--white);font-size:11px}
.card .buy{position:absolute;right:12px;bottom:18px;width:54px;height:30px;background:var(--accent);color:var(--white);font-weight:700;font-size:13px;display:flex;align-items:center;justify-content:center}
.c1{left:132px}.c2{left:451px}.c3{left:771px}

/* how it works */
.how{left:0;top:2909px;width:1200px;height:503px;background:var(--band)}
.how-title{left:0;top:2970px;width:1200px;text-align:center;font-family:"Montserrat",sans-serif;font-weight:700;font-size:25px}
.how-rule{left:547px;top:3020px;width:106px;height:1px;background:var(--grey)}
.step-art{width:150px;height:150px;top:3092px;border-radius:8px}
.step-label{top:3285px;width:240px;text-align:center;font-size:16px;line-height:28px;color:var(--ink)}

/* footer */
.f-brand{left:132px;top:3486px;display:flex;align-items:center;gap:9px;font-family:"Montserrat",sans-serif;font-weight:800;font-size:24px;color:var(--ink)}
.f-brand .brand-dot{background:var(--ink);width:16px;height:16px}
.follow{left:132px;top:3578px;width:230px;text-align:center;font-size:11px;font-weight:600}
.f-social{left:195px;top:3620px}
.f-social span{width:28px;height:28px}
.f-col{top:3468px;font-size:11px;line-height:20px;color:var(--text)}
.f-col h4{font-size:11px;font-weight:600;color:var(--ink);margin-bottom:16px}
.news-input{left:798px;top:3509px;width:267px;height:48px;border:1px solid var(--grey);display:flex;align-items:center;font-size:12px;color:#555}
.news-input svg{margin:0 14px 0 20px}
.news-btn{left:956px;top:3576px;width:109px;height:42px;background:var(--ink);color:var(--white);font-weight:700;font-size:15px;display:flex;align-items:center;justify-content:center}
.f-rule{left:132px;top:3722px;width:933px;height:1px;background:var(--line)}
.copy{left:0;top:3776px;width:1200px;text-align:center;font-size:10px;color:var(--text)}
</style>
</head>
<body>

<!-- hero -->
<div class="abs hero" role="img" aria-label="Concert crowd with raised hands under bright orange stage lights"></div>
<header class="abs topbar"></header>
<div class="abs brand" style="z-index:4"><span class="brand-dot"></span>BROVLANE PASS</div>
<nav class="abs nav" style="z-index:4">
  <a class="active" href="#">Home</a><a href="#">How to Order</a><a href="#">About us</a><a href="#">Contact us</a><a href="#">Policies</a><a href="#">Privacy</a><a href="#">Center Sale</a><a href="#">Access</a>
  <div class="social" aria-label="Social links"><span></span><span></span><span></span></div>
</nav>
<h1 class="abs hero-title">Buy and sell tickets for your favourite events</h1>
<div class="abs search">
  <svg width="14" height="14" viewBox="0 0 14 14"><circle cx="6" cy="6" r="4.5" fill="none" stroke="#1b1b1b" stroke-width="1.8"/><line x1="9.3" y1="9.3" x2="13" y2="13" stroke="#1b1b1b" stroke-width="1.8"/></svg>
  <span class="field">Search for Event</span>
  <span class="go">SEARCH</span>
</div>
<div class="abs dots"><i></i><i class="on"></i><i></i><i></i><i></i></div>

<!-- upcoming -->
<h2 class="abs sec-title" style="top:734px">UPCOMING EVENTS</h2>
<div class="abs date-pick">SELECT DATE<b>20/03/2017</b>
  <svg width="16" height="16" viewBox="0 0 16 16"><rect x="1.5" y="3" width="13" height="11.5" fill="none" stroke="#1b1b1b" stroke-width="1.4"/><line x1="1.5" y1="6.5" x2="14.5" y2="6.5" stroke="#1b1b1b" stroke-width="1.4"/><line x1="5" y1="1" x2="5" y2="4" stroke="#1b1b1b" stroke-width="1.4"/><line x1="11" y1="1" x2="11" y2="4" stroke="#1b1b1b" stroke-width="1.4"/></svg>
</div>

<div class="abs card c1" style="top:823px"><div class="photo" role="img" aria-label="Arena concert with blue stage lights" style="background:linear-gradient(160deg,#3aa0ff,#10306a 55%,#050a1c)"></div><div class="shade"></div><div class="date"><b>20</b><small>March</small><em>2:00</em></div><h3>LOREM IPSUM IS SIMPLY</h3><p>It is a long established</p><span class="buy">BUY</span></div>
<div class="abs card c2" style="top:823px"><div class="photo" role="img" aria-label="Festival performers on an outdoor stage" style="background:linear-gradient(160deg,#c9b7a6,#9a4b3c 55%,#3b2420)"></div><div class="shade"></div><div class="date"><b>20</b><small>March</small><em>2:00</em></div><h3>LOREM IPSUM IS SIMPLY</h3><p>It is a long established</p><span class="buy">BUY</span></div>
<div class="abs card c3" style="top:823px"><div class="photo" role="img" aria-label="Crowd dancing under purple confetti light" style="background:linear-gradient(160deg,#c7c3ea,#5a4f8e 50%,#1a1530)"></div><div class="shade"></div><div class="date"><b>20</b><small>March</small><em>2:00</em></div><h3>LOREM IPSUM IS SIMPLY</h3><p>It is a long established</p><span class="buy">BUY</span></div>

<div class="abs card c1" style="top:1160px"><div class="photo" role="img" aria-label="Friends celebrating at a summer festival" style="background:linear-gradient(160deg,#e9dcc0,#b78a5a 50%,#4a3520)"></div><div class="shade"></div><div class="date"><b>20</b><small>March</small><em>2:00</em></div><h3>LOREM IPSUM IS SIMPLY</h3><p>It is a long established</p><span class="buy">BUY</span></div>
<div class="abs card c2" style="top:1160px"><div class="photo" role="img" aria-label="Traditional dancer in a golden headdress" style="background:linear-gradient(160deg,#5a6a7a,#8a6a2a 50%,#2a1a10)"></div><div class="shade"></div><div class="date"><b>20</b><small>March</small><em>2:00</em></div><h3>LOREM IPSUM IS SIMPLY</h3><p>It is a long established</p><span class="buy">BUY</span></div>
<div class="abs card c3" style="top:1160px"><div class="photo" role="img" aria-label="Open air show beside a castle at dusk" style="background:linear-gradient(170deg,#b6c0c8,#6e6a5a 45%,#3a2a1c)"></div><div class="shade"></div><div class="date"><b>20</b><small>March</small><em>2:00</em></div><h3>LOREM IPSUM IS SIMPLY</h3><p>It is a long established</p><span class="buy">BUY</span></div>

<!-- concerts -->
<h2 class="abs sec-title" style="top:1518px">CONCERTS</h2>
<div class="abs view-all" style="top:1521px">VIEW ALL CONCERTS</div>
<div class="abs card c1" style="top:1605px"><div class="photo" role="img" aria-label="Concert crowd under red stage lights" style="background:linear-gradient(170deg,#ff8a6a,#b5321c 45%,#2a0a06)"></div><div class="shade"></div><div class="date"><b>18</b><small>March</small><em>0:50</em></div><h3>LOREM IPSUM IS SIMPLY</h3><p>It is a long established</p><span class="buy">BUY</span></div>
<div class="abs card c2" style="top:1605px"><div class="photo" role="img" aria-label="Guitarist playing on a dark stage" style="background:linear-gradient(160deg,#3a3a3a,#6a5540 50%,#0e0c0a)"></div><div class="shade"></div><div class="date"><b>25</b><small>March</small><em>1:28</em></div><h3>LOREM IPSUM IS SIMPLY</h3><p>It is a long established</p><span class="buy">BUY</span></div>
<div class="abs card c3" style="top:1605px"><div class="photo" role="img" aria-label="Cheering fan at a lit-up concert" style="background:linear-gradient(160deg,#f0c890,#a85a3a 50%,#30140c)"></div><div class="shade"></div><div class="date"><b>31</b><small>March</small><em>2:00</em></div><h3>LOREM IPSUM IS SIMPLY</h3><p>It is a long established</p><span class="buy">BUY</span></div>

<!-- theater -->
<h2 class="abs sec-title" style="top:1986px">THEATER</h2>
<div class="abs view-all" style="top:1989px">VIEW ALL THEATER SHOWS</div>
<div class="abs card c1" style="top:2070px"><div class="photo" role="img" aria-label="Dramatic theatre makeup in grey tones" style="background:linear-gradient(160deg,#8a8a8a,#3a3a3a 55%,#0a0a0a)"></div><div class="shade"></div><div class="date"><b>18</b><small>March</small><em>0:50</em></div><h3>LOREM IPSUM IS SIMPLY</h3><p>It is a long established</p><span class="buy">BUY</span></div>
<div class="abs card c2" style="top:2070px"><div class="photo" role="img" aria-label="Theatre building facade with show banner" style="background:linear-gradient(170deg,#7a8ea0,#8a4a38 45%,#2a1a14)"></div><div class="shade"></div><div class="date"><b>25</b><small>March</small><em>1:28</em></div><h3>LOREM IPSUM IS SIMPLY</h3><p>It is a long established</p><span class="buy">BUY</span></div>
<div class="abs card c3" style="top:2070px"><div class="photo" role="img" aria-label="Costumed stage wizard in white robes" style="background:linear-gradient(160deg,#d8dde2,#8a9098 50%,#2a2e34)"></div><div class="shade"></div><div class="date"><b>31</b><small>March</small><em>2:00</em></div><h3>LOREM IPSUM IS SIMPLY</h3><p>It is a long established</p><span class="buy">BUY</span></div>

<!-- sports -->
<h2 class="abs sec-title" style="top:2466px">SPORTS</h2>
<div class="abs view-all" style="top:2469px">VIEW ALL SPORTS SHOWS</div>
<div class="abs card c1" style="top:2548px"><div class="photo" role="img" aria-label="Cyclist racing in red kit" style="background:linear-gradient(160deg,#4a4a4a,#7a2a24 50%,#0c0c0c)"></div><div class="shade"></div><div class="date"><b>18</b><small>March</small><em>0:50</em></div><h3>LOREM IPSUM IS SIMPLY</h3><p>It is a long established</p><span class="buy">BUY</span></div>
<div class="abs card c2" style="top:2548px"><div class="photo" role="img" aria-label="Basketball player leaping to the hoop" style="background:linear-gradient(160deg,#3a4a6a,#8a2a2a 55%,#0a0a14)"></div><div class="shade"></div><div class="date"><b>25</b><small>March</small><em>1:28</em></div><h3>LOREM IPSUM IS SIMPLY</h3><p>It is a long established</p><span class="buy">BUY</span></div>
<div class="abs card c3" style="top:2548px"><div class="photo" role="img" aria-label="Group of athletes from different sports" style="background:linear-gradient(160deg,#c8ccd2,#8a6a5a 50%,#2a2020)"></div><div class="shade"></div><div class="date"><b>31</b><small>March</small><em>2:00</em></div><h3>LOREM IPSUM IS SIMPLY</h3><p>It is a long established</p><span class="buy">BUY</span></div>

<!-- how it works -->
<section class="abs how"></section>
<h2 class="abs how-title">HOW IT WORKS</h2>
<div class="abs how-rule"></div>
<svg class="abs" style="left:0;top:3060px" width="1200" height="220" viewBox="0 0 1200 220" fill="none" stroke="#555" stroke-width="1.5" stroke-dasharray="4 5">
  <path d="M300 60 Q345 0 395 50"/><path d="M530 170 Q600 240 680 170"/><path d="M820 40 Q880 -5 940 45"/>
</svg>
<div class="abs step-art" style="left:133px;background:linear-gradient(135deg,#d9eef4,#f3d6cf)" role="img" aria-label="Illustration of a checklist being filled in"></div>
<div class="abs step-art" style="left:385px;background:linear-gradient(135deg,#f3d6cf,#d9eef4)" role="img" aria-label="Illustration of a computer showing an online box office"></div>
<div class="abs step-art" style="left:677px;background:linear-gradient(135deg,#d9eef4,#f7ecc8)" role="img" aria-label="Illustration of a hand holding a payment card"></div>
<div class="abs step-art" style="left:925px;background:linear-gradient(135deg,#f3d6cf,#dedede)" role="img" aria-label="Illustration of a calendar, clock and gear"></div>
<div class="abs step-label" style="left:88px">Signup and create<br>your Event</div>
<div class="abs step-label" style="left:337px">Publish your<br>online box office</div>
<div class="abs step-label" style="left:622px">Start Buying<br>Tickets</div>
<div class="abs step-label" style="left:871px">Manage attendees<br>to your event</div>

<!-- footer -->
<footer>
  <div class="abs f-brand"><span class="brand-dot"></span>BROVLANE PASS</div>
  <div class="abs follow">FOLLOW US</div>
  <div class="abs social f-social" aria-label="Social links"><span></span><span></span><span></span></div>
  <div class="abs f-col" style="left:442px"><h4>MENU</h4>Home<br>How to Order<br>About us<br>Contact us<br>Policies, Privacy<br>Center Sale<br>Access</div>
  <div class="abs f-col" style="left:636px"><h4>LINKS</h4>My Account<br>FAQ<br>Login<br>Register</div>
  <div class="abs f-col" style="left:798px"><h4>NEWSLETTER SIGNUP!</h4></div>
  <div class="abs news-input">
    <svg width="16" height="12" viewBox="0 0 16 12"><rect x="1" y="1" width="14" height="10" fill="none" stroke="#1b1b1b" stroke-width="1.3"/><path d="M1 1 L8 7 L15 1" fill="none" stroke="#1b1b1b" stroke-width="1.3"/></svg>E-mail id
  </div>
  <div class="abs news-btn">SIGNUP!</div>
  <div class="abs f-rule"></div>
  <div class="abs copy">Copyright© 2017 All Rights Reserved</div>
</footer>

</body>
</html>
```